Private launch of Dozora, the smart baby sleep tracker

We need a webpage/website to initiate the Private launch of Dozora, our baby sleep tracker.

Meet Dozora:
Sleep, or rather the lack of sleep, is the one of the most challenging aspect of caring for a newborn in the first year. Recently, phone apps for baby tracking have taken hold. But those continue requiring parents to manually enter sleep and awake time. Sleep-deprived parents need a safe, automatic, accurate and stress-free tracking system. Therefore, we provide an affordable smart wearable to track baby’s sleep based on baby’s vital signs.

Target Market(s)

new parents with infants

Industry/Entity Type

Baby Care

Number of Pages Required

1 page

Font styles to use
Sans Serif

Colors
85cae6
f8ba93

Requirements
Must have
• Dozora baby sleep tracker, demonstration video, payment and ordering information. Introduction of our company "Vantor Bright Digital".
• Considering the primary targets are sleep-deprived new parents, the webpage should be user-friendly.
Nice to have
• Product rating and reviews

```html
<!DOCTYPE html>
<html lang="en">
<head>
<meta charset="utf-8">
<title>Dozora – Smart Baby Sleep Tracker</title>
<link href="https://fonts.googleapis.com/css2?family=Montserrat:wght@400;500;600;700&family=Open+Sans:wght@400;600&display=swap" rel="stylesheet">
<style>
:root{
  --sky:#85cae6;
  --peach:#f8ba93;
  --teal:#5f9fb5;
  --teal-dark:#4b889e;
  --footer:#2f4b57;
  --footer-deep:#263f49;
  --ink:#3d4a52;
  --muted:#7b868c;
  --white:#ffffff;
}
*{box-sizing:border-box;margin:0;padding:0}
html,body{width:1200px;height:5217px;overflow:hidden}
body{font-family:"Open Sans",sans-serif;color:var(--ink);background:var(--white);font-size:14px;line-height:1.6}
h1,h2,h3,h4,.btn,.nav-menu,.brand{font-family:"Montserrat",sans-serif}
.btn{display:inline-block;background:var(--sky);color:var(--white);font-size:12px;font-weight:600;letter-spacing:1px;text-transform:uppercase;padding:12px 30px;border-radius:2px}
.btn-peach{background:var(--peach)}

.topbar{height:44px;background:var(--white);border-bottom:1px solid #eee;display:flex;align-items:center;justify-content:space-between;padding:0 40px;font-size:12px;color:var(--muted)}
.topbar .shipping{display:flex;align-items:center;gap:8px}
.topbar .account{display:flex;align-items:center;gap:16px}
.topbar .cart{display:flex;align-items:center;gap:4px;color:var(--peach);font-weight:600}

.site-nav{height:80px;display:flex;align-items:center;justify-content:space-between;padding:0 40px;background:var(--white)}
.brand{display:flex;align-items:center;gap:10px;font-size:26px;font-weight:700;color:var(--peach)}
.brand-dot{width:22px;height:22px;border-radius:50%;background:var(--sky)}
.nav-menu{display:flex;gap:30px;font-size:12px;font-weight:600;text-transform:uppercase;color:var(--ink)}
.nav-menu .active{color:var(--sky)}

.hero{position:relative;height:496px;background:linear-gradient(180deg,rgba(0,0,0,0) 40%,rgba(60,50,50,.28) 100%),linear-gradient(100deg,#cfc6c2 0%,#e3d8d4 35%,#e7c9c9 60%,#d9b8bc 100%)}
.hero-text{position:absolute;left:56px;top:282px;width:470px}
.hero-text h1{font-size:30px;font-weight:500;line-height:1.3;color:var(--white);text-shadow:0 2px 8px rgba(0,0,0,.45);margin-bottom:26px}

.section-title{font-size:34px;font-weight:500;text-align:center}

.why{height:430px;background:var(--teal);color:var(--white);padding-top:58px}
.feature-row{display:flex;justify-content:center;gap:120px;margin-top:50px}
.feature{width:200px;text-align:center;font-size:14px;line-height:1.5}
.feature-img{width:130px;height:130px;border-radius:50%;margin:0 auto 18px;border:4px solid rgba(255,255,255,.5)}

.about{height:595px;display:flex}
.about-photo{width:450px;height:100%;background:linear-gradient(160deg,#e6e3e0,#cdc6c2 55%,#b7aaa6)}
.about-body{flex:1;padding:70px 90px 0 80px;text-align:center}
.about-body h2{font-size:34px;font-weight:500;margin-bottom:28px}
.about-body p{font-size:14px;color:var(--muted);margin-bottom:24px}

.parents{height:420px;background:linear-gradient(90deg,#eef0f1,#f7f5f3 40%,#e6e1dd 100%);text-align:center;padding-top:110px}
.parents h2{font-size:44px;font-weight:500;color:var(--teal-dark)}
.parents p{font-family:"Montserrat",sans-serif;font-size:20px;color:var(--ink);margin:4px 0 28px}

.night{height:600px;display:flex}
.night-side{width:450px;text-align:center;padding-top:56px}
.night-side h3{font-size:24px;font-weight:500;color:var(--teal-dark)}
.night-side p{color:var(--muted);font-size:14px}
.phone-shot{width:240px;height:430px;margin:30px auto 0;border-radius:28px;background:linear-gradient(180deg,#c9e7f2,#85cae6 60%,#e6d6cc)}
.how{flex:1;background:linear-gradient(120deg,rgba(95,159,181,.92),rgba(133,202,230,.85));color:var(--white);text-align:center;padding:90px 70px 0}
.how h2{font-size:38px;font-weight:500;margin-bottom:22px}
.how p{font-size:14px;line-height:1.7;margin-bottom:40px}
.play{display:block;margin:0 auto}

.advantage{height:480px;background:var(--teal);color:var(--white);text-align:center;padding-top:60px}
.advantage .lead{width:640px;margin:18px auto 0;font-size:14px}
.adv-row{display:flex;justify-content:center;gap:140px;margin-top:50px}
.adv{width:180px;font-size:14px}
.adv-img{width:120px;height:120px;border-radius:50%;margin:0 auto 16px;background:var(--white)}

.reviews{height:1745px;padding-top:64px;text-align:center;position:relative}
.reviews h2{font-size:38px;font-weight:500}
.reviews .lead{width:640px;margin:16px auto 0;font-size:14px;color:var(--muted)}
.review-grid{display:flex;justify-content:center;gap:26px;margin-top:60px;text-align:left;height:1250px}
.review-col{width:250px;display:flex;flex-direction:column;justify-content:space-between;height:100%}
.review-col.offset{padding-top:90px}
.review-card{background:var(--white);box-shadow:0 3px 14px rgba(0,0,0,.14)}
.review-body{padding:18px 18px 22px}
.review-body h4{font-size:18px;font-weight:500;line-height:1.3;margin-bottom:6px}
.stars{color:var(--peach);font-size:15px;letter-spacing:2px}
.review-body .who{font-size:11px;color:var(--muted);margin:2px 0 6px}
.review-body p{font-size:12px;color:var(--muted);line-height:1.6}
.reviews .more{position:absolute;left:50%;transform:translateX(-50%);top:1620px}

.site-footer{height:327px;background:var(--footer);color:#c9d6db;position:relative}
.footer-cols{display:flex;gap:60px;padding:48px 160px 0}
.footer-cols h4{font-size:15px;font-weight:600;color:var(--white);margin-bottom:12px}
.footer-cols li{list-style:none;font-size:12px;line-height:1.9}
.col-contact{width:280px}
.col-links{width:110px}
.col-account{width:160px}
.col-news{width:240px;font-size:12px}
.socials{display:flex;gap:8px;margin-top:12px}
.socials span{width:22px;height:22px;border-radius:50%;background:var(--teal)}
.news-input{height:30px;background:var(--white);margin:10px 0;border-radius:2px}
.col-news .btn{padding:8px 20px;font-size:11px}
.pay-row{display:flex;justify-content:center;gap:10px;position:absolute;left:0;right:0;top:232px}
.pay-row span{width:48px;height:28px;border-radius:3px;background:#e8eef0}
.order-btn{position:absolute;right:160px;top:232px;padding:8px 26px;font-size:11px}
.copyright{position:absolute;left:0;right:0;bottom:0;height:44px;background:var(--footer-deep);text-align:center;line-height:44px;font-size:12px}
</style>
</head>
<body>

<div class="topbar">
  <div class="shipping">
    <svg width="18" height="14" viewBox="0 0 18 14"><rect x="1" y="2" width="10" height="8" fill="none" stroke="#f8ba93" stroke-width="1.5"/><path d="M11 5h4l2 3v2h-6z" fill="none" stroke="#f8ba93" stroke-width="1.5"/><circle cx="5" cy="12" r="1.5" fill="#f8ba93"/><circle cx="14" cy="12" r="1.5" fill="#f8ba93"/></svg>
    Free Shipping
  </div>
  <div class="account">
    <span>Login / Register</span>
    <span class="cart">
      <svg width="16" height="14" viewBox="0 0 16 14"><path d="M1 1h3l2 8h8l1-6H5" fill="none" stroke="#f8ba93" stroke-width="1.5"/><circle cx="7" cy="12" r="1.3" fill="#f8ba93"/><circle cx="13" cy="12" r="1.3" fill="#f8ba93"/></svg>
      0
    </span>
  </div>
</div>

<header class="site-nav">
  <div class="brand"><span class="brand-dot"></span>Vantor Bright</div>
  <nav class="nav-menu">
    <span class="active">Home</span><span>About Us</span><span>Products</span><span>Features</span><span>Reviews</span><span>Contact Us</span>
  </nav>
</header>

<section class="hero" role="img" aria-label="Photo of a baby in a pink knitted hat sleeping on a soft blanket">
  <div class="hero-text">
    <h1>We provide an affordable smart wearable to track baby's sleep</h1>
    <span class="btn">Buy Now</span>
  </div>
</section>

<section class="why">
  <h2 class="section-title">Why Choose Dozora</h2>
  <div class="feature-row">
    <div class="feature">
      <div class="feature-img" role="img" aria-label="Photo of the wearable band and its charging base" style="background:linear-gradient(135deg,#f2f5f6,#cfe3ea)"></div>
      Wearable designed for infant<br>Medical grade hardware<br>Organic cotton strap
    </div>
    <div class="feature">
      <div class="feature-img" role="img" aria-label="Photo of a sleeping baby" style="background:linear-gradient(135deg,#f2dcd0,#d9b7a6)"></div>
      Cloud AI to learn, analyze and predict sleep patterns
    </div>
    <div class="feature">
      <div class="feature-img" role="img" aria-label="Sleep tracking chart on a light screen" style="background:linear-gradient(135deg,#ffffff,#b8e2f0)"></div>
      Automatic sleep tracking
    </div>
  </div>
</section>

<section class="about">
  <div class="about-photo" role="img" aria-label="Photo of a baby in a grey hat and red outfit lying on a white blanket"></div>
  <div class="about-body">
    <h2>About Vantor Bright Digital</h2>
    <p>We are a small team of parents and engineers who build calm, simple tools for families. Our sleep wearable reads gentle vital signs so you never have to log a nap by hand again, giving tired parents a clear view of each night.</p>
    <p>Every device is tested for safety, made with soft organic materials and backed by friendly support from people who have been there too.</p>
    <span class="btn">Read More</span>
  </div>
</section>

<section class="parents" role="img" aria-label="Faded photo of a baby wrapped in a knitted blanket">
  <h2>90% of Parents</h2>
  <p>say they get more sleep with Dozora</p>
  <span class="btn">Buy Now</span>
</section>

<section class="night">
  <div class="night-side">
    <h3>Your Night with Dozora</h3>
    <p>Quiet nights with gentle tracking</p>
    <div class="phone-shot" role="img" aria-label="Photo of a hand holding a phone showing the Dozora sleep app"></div>
  </div>
  <div class="how" role="img" aria-label="Video still of a parent holding a sleeping baby, tinted blue">
    <h2>How It Works</h2>
    <p>Clip the soft band on your baby's ankle and let it rest. Dozora quietly reads heart rate and movement, sends the data to the app and shows you when sleep starts, stops and how deep it was, all without a single tap from you.</p>
    <svg class="play" width="80" height="80" viewBox="0 0 80 80" aria-label="Play demonstration video"><circle cx="40" cy="40" r="38" fill="#ffffff"/><path d="M32 25 L57 40 L32 55 Z" fill="#f8ba93"/></svg>
  </div>
</section>

<section class="advantage">
  <h2 class="section-title">Advantage of Dozora</h2>
  <p class="lead">Simple, safe and caring design that fits into your routine, so you can rest easier while your baby sleeps soundly through the night.</p>
  <div class="adv-row">
    <div class="adv"><div class="adv-img" role="img" aria-label="Photo of the band on a baby's foot" style="background:linear-gradient(135deg,#ffffff,#f3d9cb)"></div>Carefree<br>Auto Tracking</div>
    <div class="adv"><div class="adv-img" role="img" aria-label="Photo of the sensor in a hand" style="background:linear-gradient(135deg,#ffffff,#d6e9f0)"></div>Accurate and<br>affordable</div>
    <div class="adv"><div class="adv-img" role="img" aria-label="Illustration of a growth calendar" style="background:linear-gradient(135deg,#ffffff,#e8eef0)"></div>Grow with the<br>baby</div>
  </div>
</section>

<section class="reviews">
  <h2>Reviews</h2>
  <p class="lead">Real stories from families who sleep better since bringing Dozora home.</p>
  <div class="review-grid">
    <div class="review-col">
      <article class="review-card">
        <div role="img" aria-label="Photo of a baby in a knitted hat" style="height:210px;background:linear-gradient(135deg,#d7d2cf,#a9a29f)"></div>
        <div class="review-body"><h4>Finally we sleep through the night</h4><div class="stars">★★★★★</div><div class="who">Anna</div><p>Set up in minutes and we stopped writing naps in a notebook.</p></div>
      </article>
      <article class="review-card">
        <div role="img" aria-label="Photo of a sleeping baby" style="height:190px;background:linear-gradient(135deg,#f1e0d6,#d8bcae)"></div>
        <div class="review-body"><h4>Soft band, clear app</h4><div class="stars">★★★★★</div><div class="who">Mark</div><p>Our son never notices the band and the charts are easy to read.</p></div>
      </article>
      <article class="review-card">
        <div class="review-body"><h4>Worth every penny for us</h4><div class="stars">★★★★★</div><div class="who">Leah</div><p>The sleep patterns helped us plan naps around daycare. We feel calmer, rested and more sure of our routine every single week now.</p></div>
      </article>
    </div>
    <div class="review-col offset">
      <article class="review-card">
        <div role="img" aria-label="Photo of a baby asleep on a white pillow" style="height:220px;background:linear-gradient(135deg,#e9eef0,#c3d3da)"></div>
        <div class="review-body"><h4>Peace of mind at night</h4><div class="stars">★★★★★</div><div class="who">Sara</div><p>I check the app instead of tiptoeing into the nursery.</p></div>
      </article>
      <article class="review-card">
        <div role="img" aria-label="Photo of a baby sleeping on a blanket" style="height:200px;background:linear-gradient(135deg,#f3e6de,#d9c3b6)"></div>
        <div class="review-body"><h4>Great for tired parents</h4><div class="stars">★★★★★</div><div class="who">Tom</div><p>No more guessing how long she slept. It all just shows up.</p></div>
      </article>
      <article class="review-card">
        <div class="review-body"><h4>Simple and reliable</h4><div class="stars">★★★★★</div><div class="who">Nina</div><p>Battery lasts days and the band washes well. Support replied fast when I had a question.</p></div>
      </article>
    </div>
    <div class="review-col" style="justify-content:flex-start;gap:40px">
      <article class="review-card">
        <div role="img" aria-label="Photo of parents sitting together with a tablet" style="height:230px;background:linear-gradient(135deg,#efe6df,#c9b7ab)"></div>
        <div class="review-body"><h4>Both of us love it</h4><div class="stars">★★★★★</div><div class="who">Chris</div><p>We share the app and finally agree on the bedtime plan.</p></div>
      </article>
      <article class="review-card">
        <div role="img" aria-label="Photo of a parent using a tablet on the sofa" style="height:230px;background:linear-gradient(135deg,#e4e2df,#b3aca6)"></div>
        <div class="review-body"><h4>Smart and gentle design</h4><div class="stars">★★★★★</div><div class="who">Priya</div><p>The weekly report showed us how small changes made sleep longer. A thoughtful gift for any new parent.</p></div>
      </article>
    </div>
  </div>
  <span class="btn more">View More</span>
</section>

<footer class="site-footer">
  <div class="footer-cols">
    <div class="col-contact">
      <h4>Contact Us</h4>
      <ul>
        <li>48 Willow Lane, Brookfield</li>
        <li>Open Monday to Friday</li>
        <li>☎ 202-555-0148</li>
        <li>✉ hello@vantorbright.example</li>
      </ul>
      <div class="socials"><span></span><span></span><span></span><span></span></div>
    </div>
    <div class="col-links">
      <h4>Links</h4>
      <ul><li>Home</li><li>About</li><li>Products</li><li>Reviews</li></ul>
    </div>
    <div class="col-account">
      <h4>Your account</h4>
      <ul><li>Track an Order</li><li>Returns &amp; Refunds</li><li>Delivery Information</li><li>Easy Ways to Pay</li></ul>
    </div>
    <div class="col-news">
      <h4>Newsletter</h4>
      <p>Subscribe to our newsletter for latest updates</p>
      <div class="news-input"></div>
      <span class="btn btn-peach">Subscribe</span>
    </div>
  </div>
  <div class="pay-row" aria-label="Accepted payment methods"><span></span><span></span><span></span><span></span></div>
  <span class="btn btn-peach order-btn">Order Now</span>
  <div class="copyright">© 2024 Vantor Bright Digital. All rights reserved.</div>
</footer>

</body>
</html>
```